New Business Card Design Project LORVANTI-Italy

we are LORVANTI-Italy
our company in the market for 3 years we are luxury cosmetic company and its about time for a facelift :)
i will like to have elegant luxurious and unique business card
that will give the person that get it a unique, luxurious and elegant impression
I'm VERY OPEN FOR NEW IDEAS , even duo i add a few files of things that i see on line and i like them

i add my logo as well
my website is LORVANTI.COM
(if you would like to see the main style that we have)

Target Market(s)

adult that have money :)

Industry/Entity Type

Business

Contact Information for Business Card

Name - Dario Lorvanti
Position - CEO and CO Founder
address - 4817 E Halvern
telephone - 555-384-1926
email - dario@lorvanti.com
fax - 555-384-1926
website - LORVANTI.COM

Colors
000000
959595
fbee3e
ffffff

Requirements
Must have
• big logo in GOLD color
• elegant look
• impressive
Nice to have
• not must but maybe classy pattern background
• not must but maybe emblem
• maybe clear plastic business card
Should not have
• colors
• images

```html
<!DOCTYPE html>
<html lang="en">
<head>
<meta charset="utf-8">
<title>LORVANTI Italy – Business Card</title>
<link rel="stylesheet" href="https://fonts.googleapis.com/css2?family=Marcellus&family=Open+Sans:wght@400&display=swap">
<style>
  :root {
    --backdrop: #3b3c40;
    --card: #0c0c0d;
    --gold: #d9ab2e;
    --gold-soft: #c99a25;
    --white: #f2f2f2;
    --rule: #3a3a3a;
  }
  html, body {
    margin: 0;
    width: 1200px;
    height: 864px;
    overflow: hidden;
    background: var(--backdrop);
  }
  .canvas {
    position: relative;
    width: 1200px;
    height: 864px;
  }
  .card {
    position: absolute;
    width: 600px;
    height: 340px;
    background: var(--card);
    box-shadow: 0 10px 28px rgba(0,0,0,.45);
    font-family: "Open Sans", sans-serif;
    color: var(--white);
  }
  .card--front { left: 210px; top: 70px; }
  .card--back  { left: 250px; top: 450px; }

  /* Front */
  .front-mark {
    position: absolute;
    left: 50%;
    top: 40px;
    width: 96px;
    height: 96px;
    margin-left: -48px;
    border: 2px solid var(--gold);
    border-radius: 50%;
    box-sizing: border-box;
  }
  .brand {
    font-family: "Marcellus", serif;
    color: var(--gold);
    text-align: center;
    line-height: 1;
  }
  .brand__name { font-size: 46px; letter-spacing: 1px; }
  .brand__region { font-size: 17px; letter-spacing: 2px; margin-top: 12px; }
  .card--front .brand {
    position: absolute;
    left: 0; right: 0;
    top: 154px;
  }
  .front-web {
    position: absolute;
    left: 0; right: 0;
    top: 282px;
    text-align: center;
    font-family: "Marcellus", serif;
    color: var(--gold);
    font-size: 13px;
    letter-spacing: 1px;
  }

  /* Back */
  .card--back .brand {
    position: absolute;
    right: 50px;
    top: 34px;
    width: 300px;
  }
  .card--back .brand__name { font-size: 48px; }
  .divider {
    position: absolute;
    left: 70px;
    right: 60px;
    top: 180px;
    border-top: 1px solid var(--rule);
  }
  .holder {
    position: absolute;
    left: 60px;
    top: 130px;
  }
  .holder__name {
    font-family: "Marcellus", serif;
    color: var(--gold);
    font-size: 19px;
    letter-spacing: 1px;
  }
  .holder__role { font-size: 13px; margin-top: 2px; }
  .address {
    position: absolute;
    left: 56px;
    top: 216px;
    font-size: 13px;
  }
  .contacts {
    position: absolute;
    right: 40px;
    top: 232px;
    list-style: none;
    margin: 0;
    padding: 0;
    font-size: 14px;
    text-align: right;
  }
  .contacts li {
    display: flex;
    justify-content: flex-end;
    align-items: center;
    gap: 8px;
    height: 22px;
  }
  .contacts svg { width: 12px; height: 12px; fill: var(--gold-soft); }
</style>
</head>
<body>
<main class="canvas">

  <section class="card card--front" aria-label="Card front">
    <div class="front-mark"></div>
    <div class="brand">
      <div class="brand__name">LORVANTI</div>
      <div class="brand__region">ITALY</div>
    </div>
    <div class="front-web">WWW.LORVANTI.COM</div>
  </section>

  <section class="card card--back" aria-label="Card back">
    <div class="brand">
      <div class="brand__name">LORVANTI</div>
      <div class="brand__region">ITALY</div>
    </div>
    <div class="holder">
      <div class="holder__name">DARIO LORVANTI</div>
      <div class="holder__role">CEO and CO Founder</div>
    </div>
    <div class="divider"></div>
    <div class="address">4817 E Halvern</div>
    <ul class="contacts">
      <li>555-384-1926
        <svg viewBox="0 0 24 24" aria-hidden="true"><path d="M6.6 10.8a15 15 0 0 0 6.6 6.6l2.2-2.2c.3-.3.7-.4 1-.2 1.1.4 2.3.6 3.6.6.6 0 1 .4 1 1V20c0 .6-.4 1-1 1A17 17 0 0 1 3 4c0-.6.4-1 1-1h3.5c.6 0 1 .4 1 1 0 1.3.2 2.5.6 3.6.1.3 0 .7-.2 1z"/></svg>
      </li>
      <li>555-384-1926
        <svg viewBox="0 0 24 24" aria-hidden="true"><path d="M6 2h9l3 3v5H6z M3 10h18a1 1 0 0 1 1 1v9a1 1 0 0 1-1 1H3a1 1 0 0 1-1-1v-9a1 1 0 0 1 1-1zm3 3v2h4v-2zm8 0v2h2v-2zm0 4v2h2v-2z"/></svg>
      </li>
      <li>dario@lorvanti.com
        <svg viewBox="0 0 24 24" aria-hidden="true"><path d="M2 5h20v14H2z M2 5l10 8 10-8" stroke="#0c0c0d" stroke-width="1.5"/></svg>
      </li>
    </ul>
  </section>

</main>
</body>
</html>
```